SnackOrbit!!! A Vending Machine Business Looking for an attractive website.

We are a vending machine business in Northern Michigan. We have changed our name and have rebranded our company. We would like an attractive website that shares who we are, what services we provide, the products we offer in our machines, along with a form businesses can fill out to see if they are a good fit for our company. I would like to have a Home Page, About SnackOrbit, Why Choose SnackOrbit?, Products & Services, Contact Us (With a Login Option), and a page with a questionnaire for thos interested in getting a FREE Vending Machine.

Target Market(s)

Businesses, Campgrounds, Schools, and many more in Northern Michigan

Industry/Entity Type

Vending Machines

Coding

Coded - Design and coding required

Number of Pages Required

5+ page

Requirements
Must have
• An inviting and enticing Home Page. I want to get my potential clients engaged in our website.
Nice to have
• Possibly background photos from Northern Michigan
Should not have
• A corporate feel. I do not want a boring website.

```html
<!DOCTYPE html>
<html lang="en">
<head>
<meta charset="utf-8">
<title>SnackOrbit – Crave. Vend. Repeat</title>
<link href="https://fonts.googleapis.com/css2?family=Gelasio:wght@600;700&family=Outfit:wght@300;400;500;600&display=swap" rel="stylesheet">
<style>
:root{
  --navy:#23215a;
  --green:#2f5b27;
  --ink:#1c1c1c;
  --body:#333;
  --grey-bg:#f4f4f4;
  --white:#fff;
  --star:#f2a630;
}
*{margin:0;padding:0;box-sizing:border-box}
html,body{width:1200px;height:4011px;overflow:hidden}
body{position:relative;font-family:'Outfit',sans-serif;color:var(--body);background:var(--white)}
.abs{position:absolute}
.serif{font-family:'Gelasio',serif}
.btn{position:absolute;display:flex;align-items:center;justify-content:center;color:var(--white);font-size:12px;font-weight:500;border-radius:3px}
.btn--navy{background:var(--navy)}
.btn--green{background:var(--green)}
.wordmark{font-family:'Gelasio',serif;font-weight:700;color:var(--navy);white-space:nowrap;display:flex;align-items:center;gap:8px}
.wordmark .dot{display:inline-block;border-radius:50%;background:var(--green)}

/* top bar */
.topbar{left:0;top:0;width:1200px;height:39px;background:var(--navy);color:var(--white);font-size:12px;display:flex;align-items:center;justify-content:center}
.topbar b{margin-left:4px}

/* header */
.header{left:0;top:39px;width:1200px;height:86px;background:var(--white)}
.header .wordmark{position:absolute;left:140px;top:24px;font-size:34px}
.header .wordmark .dot{width:22px;height:22px}
.nav{position:absolute;left:453px;top:35px;display:flex;gap:27px;font-size:13px;color:var(--ink)}
.nav .active{color:var(--green);font-weight:600}
.header .btn{left:957px;top:26px;width:101px;height:33px}

/* hero */
.hero{left:0;top:125px;width:1200px;height:525px}
.hero-photo{position:absolute;inset:0;background:linear-gradient(100deg,#d9dde3 0%,#e9ecef 30%,#dfe5ec 55%,#c8d1dc 100%)}
.hero-machines{position:absolute;left:140px;top:128px;width:410px;height:397px;background:linear-gradient(90deg,#b8c2d6 0%,#c8333d 30%,#b5222c 60%,#c73a40 80%,#b3bdca 100%);opacity:.85}
.hero-text{position:absolute;right:141px;top:140px;text-align:right}
.hero-text .brand{font-size:46px;font-weight:500;color:var(--green);line-height:1.1}
.hero-text .brand span{color:var(--navy)}
.hero-text h1{font-size:47px;font-weight:500;color:var(--ink);line-height:1.2;margin-top:6px}
.hero-text p{font-size:22px;color:var(--ink);margin-top:12px}
.hero .btn{left:957px;top:315px;width:102px;height:33px;font-size:13px}

/* about */
.about-shadow{left:155px;top:737px;width:410px;height:410px;border-radius:50%;background:#ebebee}
.about-dots{left:143px;top:1000px;width:90px;height:120px;background-image:radial-gradient(#dcdce0 1.5px,transparent 1.6px);background-size:9px 9px}
.about-photo{left:166px;top:710px;width:404px;height:404px;border-radius:50%;background:linear-gradient(135deg,#6c6a62 0%,#a9a091 40%,#e1ddd6 65%,#8d8a85 100%)}
.about-label{left:644px;top:785px;font-size:18px;color:var(--green);font-weight:700}
.about .wordmark{position:absolute;left:638px;top:822px;font-size:38px}
.about .wordmark .dot{width:24px;height:24px}
.about-copy{left:638px;top:900px;width:420px;font-size:12px;line-height:23px;letter-spacing:.5px;color:var(--ink)}
.about-copy b{font-weight:600}
.about .btn{left:638px;top:1030px;width:123px;height:36px}

/* machines */
.machines{left:0;top:1227px;width:1200px;height:755px}
.machine-panel{position:absolute;top:0;height:755px;text-align:center;color:var(--white)}
.machine-panel--navy{left:0;width:598px;background:var(--navy)}
.machine-panel--green{left:598px;width:602px;background:var(--green)}
.machine-photo{position:absolute;top:93px;width:244px;height:412px;border-radius:3px}
.machine-panel--navy .machine-photo{left:253px;background:linear-gradient(180deg,#2b2b2e 0%,#8a7d7a 30%,#6f6364 60%,#3b3b3f 100%)}
.machine-panel--green .machine-photo{left:124px;width:212px;background:linear-gradient(180deg,#1c1c22 0%,#a84b43 30%,#3b5a8a 60%,#b54a3a 85%,#1c1c22 100%)}
.machine-panel h3{position:absolute;top:520px;width:100%;font-size:26px;font-weight:700}
.machine-panel p{position:absolute;top:562px;left:50%;transform:translateX(-50%);width:400px;font-size:12px;line-height:23px}
.machine-panel--navy p,.machine-panel--navy h3{left:auto;margin-left:-230px}
.machine-panel .btn{top:644px;width:123px;height:35px}
.machine-panel--navy .btn{left:309px}
.machine-panel--green .btn{left:169px}

/* why */
.why-title{left:0;top:2060px;width:1200px;text-align:center;font-size:40px;font-weight:700;color:var(--ink)}
.why-title span,.section-title span{color:var(--green)}
.why-card{position:absolute;top:2155px;width:173px;height:126px;background:var(--white);box-shadow:0 2px 8px rgba(0,0,0,.08);border-radius:3px;display:flex;flex-direction:column;align-items:center;justify-content:flex-end;padding-bottom:18px;text-align:center;font-size:13px;font-weight:500;color:var(--ink);line-height:15px}
.why-card svg{margin-bottom:10px}
.why-card--active{background:var(--green);color:var(--white)}
.why-card--active::after{content:"";position:absolute;bottom:-10px;left:50%;margin-left:-10px;border:10px solid transparent;border-bottom:0;border-top-color:var(--green)}
.local-title{left:145px;top:2368px;font-size:34px;font-weight:700;color:var(--ink)}
.local-copy{left:145px;top:2416px;width:420px;font-size:14px;line-height:31px;color:var(--ink)}
.local-photo{left:635px;top:2338px;width:420px;height:264px;border-radius:4px;background:linear-gradient(90deg,#0e0f14 0%,#1e2230 35%,#5b7c8e 60%,#c5bca5 80%,#7b8a97 100%)}

/* testimonials */
.testimonials{left:0;top:2698px;width:1200px;height:501px;background:var(--grey-bg)}
.section-title{position:absolute;left:0;width:1200px;text-align:center;font-size:40px;font-weight:700;color:var(--ink)}
.testimonials .section-title{top:85px}
.t-card{position:absolute;top:182px;width:444px;height:223px;background:var(--white);border-radius:4px;box-shadow:0 2px 10px rgba(0,0,0,.07);text-align:center}
.t-card::after{content:"";position:absolute;left:12px;right:12px;bottom:0;height:3px;background:var(--navy);border-radius:2px}
.t-quote{position:absolute;top:14px;left:50%;transform:translateX(-50%);font-family:'Gelasio',serif;font-size:110px;line-height:1;color:#e5e5e8}
.t-stars{position:absolute;top:72px;width:100%;color:var(--star);font-size:18px;letter-spacing:2px}
.t-text{position:absolute;top:108px;left:20px;right:20px;font-size:11px;line-height:19px;color:var(--ink)}
.t-name{position:absolute;top:178px;width:100%;font-size:15px;font-weight:700;color:var(--ink)}
.t-arrow{position:absolute;top:256px;width:36px;height:36px;border-radius:50%;display:flex;align-items:center;justify-content:center}
.t-arrow--prev{left:85px;border:1.5px solid #b8b8b8}
.t-arrow--next{left:1081px;background:var(--green)}

/* cta */
.cta-title{top:3280px;font-size:40px;line-height:52px}
.cta-copy{left:0;top:3398px;width:1200px;text-align:center;font-size:14px;line-height:26px;color:var(--ink);font-weight:500}
.cta .btn{left:543px;top:3464px;width:114px;height:37px}

/* footer */
.footer-wave{left:0;top:3596px}
.footer{left:0;top:3650px;width:1200px;height:304px;background:var(--navy);color:var(--white)}
.footer h4{position:absolute;top:70px;font-family:'Gelasio',serif;font-size:18px;font-weight:700}
.quick-links{position:absolute;left:143px;top:108px;list-style:none;font-size:12px}
.quick-links li{height:31px;display:flex;align-items:flex-start;gap:7px}
.quick-links li::before{content:"";margin-top:4px;border:3px solid transparent;border-left:4px solid var(--white);border-right:0}
.footer .wordmark{position:absolute;left:423px;top:90px;width:324px;justify-content:center;font-size:56px;color:var(--white)}
.footer .wordmark .dot{width:30px;height:30px;background:var(--white)}
.socials{position:absolute;left:517px;top:212px;display:flex;gap:6px}
.socials span{width:29px;height:29px;border:1.5px solid var(--white);border-radius:50%}
.contact-list{position:absolute;left:868px;top:108px;font-size:12px;line-height:18px}
.contact-item{display:flex;gap:10px;margin-bottom:17px}
.contact-item svg{flex:none;margin-top:2px}
.copyright{left:0;top:3954px;width:1200px;height:57px;background:var(--green);color:var(--white);font-family:'Gelasio',serif;font-size:13px;display:flex;align-items:center;justify-content:center}
</style>
</head>
<body>

<div class="abs topbar">Lorem Ipsum is simply dummy text of the printing and typesetting industry. - <b>Click Here</b></div>

<header class="abs header">
  <div class="wordmark"><span class="dot"></span>SnackOrbit</div>
  <nav class="nav">
    <span class="active">Home</span><span>About</span><span>Why Choose Us</span><span>Products &amp; Services</span><span>Contact Us</span>
  </nav>
  <a class="btn btn--navy">Log In</a>
</header>

<section class="abs hero">
  <div class="hero-photo" role="img" aria-label="Bright office hallway with vending machines and a blue bench"></div>
  <div class="hero-machines" role="img" aria-label="Row of red and glass-front vending machines"></div>
  <div class="hero-text">
    <div class="brand">SnackOrbit <span>:</span></div>
    <h1>Crave. Vend. Repeat</h1>
    <p>Elevating Snacking, One Vend at a Time</p>
  </div>
  <a class="btn btn--navy">Contact Us</a>
</section>

<section class="about">
  <div class="abs about-shadow"></div>
  <div class="abs about-dots"></div>
  <div class="abs about-photo" role="img" aria-label="Customers choosing snacks from a vending machine"></div>
  <div class="abs about-label serif">About</div>
  <div class="wordmark"><span class="dot"></span>SnackOrbit</div>
  <p class="abs about-copy">At SnackOrbit, we don’t just vend snacks—we curate cravings. Our customized vending solutions bring flavor, convenience, and community to Northern Michigan. Whether you’re reaching for a <b>mid-morning snack</b>, a <b>refreshing beverage</b>, or a <b>satisfying breakfast burrito</b>, SnackOrbit delivers delight with every bite</p>
  <a class="btn btn--green">Contact Us</a>
</section>

<section class="abs machines">
  <div class="machine-panel machine-panel--navy">
    <div class="machine-photo" role="img" aria-label="Snack vending machine stocked with chips and candy"></div>
    <h3 class="serif" style="left:0;margin-left:0">Vending Machine - 1</h3>
    <p style="left:371px;margin-left:-200px;transform:none">Lorem ipsum dolor sit amet, consectetuer adipiscing elit, sed diam nonummy nibh euismod tincidunt ut laoreet dolore magna aliquam erat volutpat. Ut wisi enim ad minim veniam.</p>
    <a class="btn btn--green">View Details</a>
  </div>
  <div class="machine-panel machine-panel--green">
    <div class="machine-photo" role="img" aria-label="Combo vending machine with snacks and bottled drinks"></div>
    <h3 class="serif">Vending Machine - 2</h3>
    <p style="transform:none;left:30px">Lorem ipsum dolor sit amet, consectetuer adipiscing elit, sed diam nonummy nibh euismod tincidunt ut laoreet dolore magna aliquam erat volutpat. Ut wisi enim ad minim veniam.</p>
    <a class="btn btn--navy">View Details</a>
  </div>
</section>

<section class="why">
  <h2 class="abs why-title serif">Why Choose <span>SnackOrbit</span></h2>
  <div class="why-card why-card--active" style="left:202px">
    <svg width="34" height="40" viewBox="0 0 34 40" fill="none" stroke="#fff" stroke-width="1.6"><path d="M17 38C9 28 3 22 3 15a14 14 0 0 1 28 0c0 7-6 13-14 23z"/><path d="M17 22l-6-6a3.5 3.5 0 0 1 6-3 3.5 3.5 0 0 1 6 3z"/></svg>
    Local Love
  </div>
  <div class="why-card" style="left:409px">
    <svg width="44" height="40" viewBox="0 0 44 40" fill="none" stroke="#23215a" stroke-width="1.6"><circle cx="18" cy="16" r="12"/><circle cx="30" cy="26" r="9" stroke="#2f5b27"/><path d="M13 14h10M13 19h8"/></svg>
    Unleash Your<br>Cravings
  </div>
  <div class="why-card" style="left:616px">
    <svg width="40" height="40" viewBox="0 0 40 40" fill="none" stroke="#23215a" stroke-width="1.6"><path d="M8 38V22h6v16zM14 24l6-10 2 2v6h10a3 3 0 0 1 0 6h-2a3 3 0 0 1 0 6H14" /><circle cx="10" cy="6" r="2.5" stroke="#2f5b27"/><circle cx="30" cy="6" r="2.5" stroke="#2f5b27"/><circle cx="20" cy="4" r="2"/></svg>
    Quality Meets<br>Convenience
  </div>
  <div class="why-card" style="left:823px">
    <svg width="40" height="40" viewBox="0 0 40 40" fill="none" stroke="#23215a" stroke-width="1.6"><path d="M4 36h32M8 36V24h5v12M17 36V18h5v12M26 36V12h5v24"/><path d="M6 18l10-8 6 4 12-10" stroke="#2f5b27"/></svg>
    Pandemic-Proof &amp;<br>Recession-Ready
  </div>
  <h3 class="abs local-title serif">Local Love</h3>
  <p class="abs local-copy">We celebrate the heart of Michigan by partnering with local legends. Say hello to Pine Ridge Jerky and Lakeshore Kettle Chips—our hometown heroes. Their flavors dance on your taste buds, and we’re thrilled to bring them straight to your workplace.</p>
  <div class="abs local-photo" role="img" aria-label="Person browsing a lit wall of vending machines at night"></div>
</section>

<section class="abs testimonials">
  <h2 class="section-title serif">What Our <span>Clients</span> Say</h2>
  <div class="t-arrow t-arrow--prev"><svg width="16" height="16" viewBox="0 0 16 16" fill="none" stroke="#999" stroke-width="1.6"><path d="M14 8H2M7 3L2 8l5 5"/></svg></div>
  <div class="t-card" style="left:142px">
    <div class="t-quote">”</div>
    <div class="t-stars">★★★★★</div>
    <p class="t-text">Lorem ipsum dolor sit amet, consectetur adipiscing elit, sed do eiusmod tempor incididunt ut labore et dolore magna aliqua. Ut enim ad minim veniam, quis nostrud exercitation ullamco laboris nisi ut aliquip ex ea</p>
    <div class="t-name serif">Nora Ellis</div>
  </div>
  <div class="t-card" style="left:615px">
    <div class="t-quote">”</div>
    <div class="t-stars">★★★★★</div>
    <p class="t-text">Lorem ipsum dolor sit amet, consectetur adipiscing elit, sed do eiusmod tempor incididunt ut labore et dolore magna aliqua. Ut enim ad minim veniam, quis nostrud exercitation ullamco laboris nisi ut aliquip ex ea</p>
    <div class="t-name serif">Sam Porter</div>
  </div>
  <div class="t-arrow t-arrow--next"><svg width="16" height="16" viewBox="0 0 16 16" fill="none" stroke="#fff" stroke-width="1.8"><path d="M2 8h12M9 3l5 5-5 5"/></svg></div>
</section>

<section class="cta">
  <h2 class="section-title cta-title serif">Ready To Experience The <span>SnackOrbit</span><br>Difference?</h2>
  <p class="abs cta-copy">Sign up now and let’s connect. Taste the future of snacking firsthand! Contact us today<br>and explore how our vending magic can elevate your space.</p>
  <a class="btn btn--green">Contact Us</a>
</section>

<svg class="abs footer-wave" width="1200" height="60" viewBox="0 0 1200 60" preserveAspectRatio="none">
  <path d="M0 58 Q600 -30 1200 58 L1200 60 L0 60Z" fill="#23215a"/>
  <path d="M0 50 Q600 -40 1200 50" fill="none" stroke="#23215a" stroke-width="3"/>
</svg>

<footer class="abs footer">
  <h4 style="left:143px">Quick Links</h4>
  <ul class="quick-links">
    <li>Home</li><li>About Us</li><li>Why Choose SnackOrbit</li><li>Product and Services</li><li>Contact Us</li>
  </ul>
  <div class="wordmark"><span class="dot"></span>SnackOrbit</div>
  <div class="socials"><span></span><span></span><span></span><span></span></div>
  <h4 style="left:868px">Contact Details</h4>
  <div class="contact-list">
    <div class="contact-item">
      <svg width="26" height="26" viewBox="0 0 26 26" fill="none" stroke="#fff" stroke-width="1.4"><circle cx="13" cy="13" r="11"/><path d="M2 13h22M13 2c4 4 4 18 0 22M13 2c-4 4-4 18 0 22"/></svg>
      <div>123, Building Name, Street<br>City, State XY 123456</div>
    </div>
    <div class="contact-item">
      <svg width="26" height="26" viewBox="0 0 26 26" fill="none" stroke="#fff" stroke-width="1.4"><path d="M6 3l4 5-2 3c1 3 4 6 7 7l3-2 5 4-2 4C12 24 2 14 2 5z"/></svg>
      <div>PHONE<br>123-456-7890</div>
    </div>
    <div class="contact-item">
      <svg width="26" height="26" viewBox="0 0 26 26" fill="none" stroke="#fff" stroke-width="1.4"><rect x="2" y="6" width="22" height="16"/><path d="M2 6l11 9 11-9"/></svg>
      <div>EMAIL<br>info@snackorbit.com</div>
    </div>
  </div>
</footer>

<div class="abs copyright">© 2024 SnackOrbit. all rights reserved.</div>

</body>
</html>
```